ULMIRA card Technical Architecture

Hello everyone ULMIRA: It is a consulting firm in Architecture and Construction. I require a card duplexing, sober, elegant, classic but not boring. Update 1: Use the following data for the card. Name: Gonzalo Pereda Mauricio Villalta Position: COO Twitter: @ulmiraAT Homepage: ulmira-example.com home address not include the participation of all thank you.

Target Market(s)

Construction companies, Architects and Consulting Engineers

Industry/Entity Type

Consulting

Contact Information for Business Card

Los campos que debe tener:
Nombre, Cargo, email, homepage y twitter

Font styles to use
Serif
Sans Serif
Other font styles liked:
• Me gustan playfair display, open sans y roboto, pero estoy sujeto a sus propuestas

Requirements
Must have
• Colors: Present combined proposals in white, red, gray and black Update 1: The two names must be clearly differentiated from the two surnames
Nice to have
• They are free to present their best proposals. I will bring them immediate feedback to the extent you can go see their designs. Complete data for card and logo files will give the winner the

```html
<!DOCTYPE html>
<html lang="es">
<head>
<meta charset="utf-8">
<title>ULMIRA – Tarjeta de presentación</title>
<link rel="stylesheet" href="https://fonts.googleapis.com/css2?family=Montserrat:wght@400;500;700&family=Open+Sans:wght@400&display=swap">
<style>
  :root {
    --bg: #e9e9e9;
    --white: #ffffff;
    --red: #c8202b;
    --red-deep: #7a0f18;
    --red-dark: #5a0a10;
    --ink: #1e1e1e;
    --gray: #4a4a4a;
    --radius: 16px;
  }
  * { margin: 0; padding: 0; box-sizing: border-box; }
  html, body { width: 1200px; height: 900px; overflow: hidden; background: var(--bg); }
  .canvas { position: relative; width: 1200px; height: 900px; }

  .card {
    position: absolute;
    width: 700px; height: 400px;
    border-radius: var(--radius);
    overflow: hidden;
    box-shadow: 0 10px 28px rgba(0,0,0,.18);
  }

  /* Back side */
  .card-back {
    left: 100px; top: 40px;
    background: radial-gradient(circle at 50% 42%, var(--red) 0%, #8e1620 45%, var(--red-dark) 100%);
    color: var(--white);
  }
  .back-brand {
    position: absolute; left: 0; right: 0; top: 150px;
    text-align: center;
    font-family: "Montserrat", sans-serif;
    font-weight: 500; font-size: 64px; letter-spacing: 14px;
    color: var(--white);
  }
  .back-social {
    position: absolute; left: 0; right: 0; top: 318px;
    display: flex; justify-content: center; align-items: center; gap: 10px;
    font-family: "Open Sans", sans-serif; font-size: 17px; color: var(--white);
  }
  .social-dot { width: 14px; height: 14px; border-radius: 50%; background: var(--white); }

  /* Front side */
  .card-front { left: 400px; top: 470px; background: var(--white); }

  .front-brand {
    position: absolute; left: 48px; top: 120px;
    display: flex; align-items: center; gap: 14px;
  }
  .brand-mark { width: 26px; height: 26px; background: var(--red); }
  .brand-name {
    font-family: "Montserrat", sans-serif; font-weight: 500;
    font-size: 40px; letter-spacing: 10px; color: var(--ink);
  }

  .person { position: absolute; right: 40px; top: 38px; text-align: right; }
  .given-names, .surnames {
    font-family: "Montserrat", sans-serif; font-weight: 700;
    font-size: 27px; color: var(--red-deep); line-height: 1.1;
  }
  .role-short {
    font-family: "Open Sans", sans-serif; font-size: 15px; color: var(--ink);
    margin-top: 2px;
  }
  .name-rule { position: absolute; left: 230px; right: 40px; top: 118px; height: 2px; background: var(--red); }
  .surname-block { position: absolute; right: 40px; top: 140px; text-align: right; }
  .role-long { font-family: "Open Sans", sans-serif; font-size: 15px; color: var(--ink); margin-top: 2px; }

  .contact-rule { position: absolute; left: 60px; top: 282px; width: 320px; height: 2px; background: var(--red); }
  .contact-bar { position: absolute; left: 230px; top: 272px; width: 150px; height: 12px; background: var(--red); }
  .accent-block {
    position: absolute; left: 396px; right: 0; top: 262px; bottom: 22px;
    background: var(--red-deep);
    clip-path: polygon(0 0, 100% 0, 100% 100%, 4% 100%);
  }
  .bottom-band { position: absolute; left: 0; right: 0; bottom: 0; height: 22px; background: var(--red); }

  .contacts {
    position: absolute; left: 60px; top: 296px;
    list-style: none;
    font-family: "Open Sans", sans-serif; font-size: 16px; color: var(--ink);
  }
  .contacts li { display: flex; align-items: center; gap: 10px; line-height: 24px; }
  .contacts svg { width: 13px; height: 13px; fill: var(--red-deep); flex: none; }
</style>
</head>
<body>
<main class="canvas">

  <section class="card card-back" aria-label="Reverso de la tarjeta">
    <div class="back-brand">ULMIRA</div>
    <div class="back-social"><span class="social-dot"></span><span>@ulmiraAT</span></div>
  </section>

  <section class="card card-front" aria-label="Anverso de la tarjeta">
    <div class="front-brand">
      <span class="brand-mark"></span>
      <span class="brand-name">ULMIRA</span>
    </div>

    <div class="person">
      <div class="given-names">Mauricio Gonzalo</div>
      <div class="role-short">COO</div>
    </div>
    <div class="name-rule"></div>
    <div class="surname-block">
      <div class="surnames">Pereda Villalta</div>
      <div class="role-long">Director de Operaciones</div>
    </div>

    <div class="accent-block"></div>
    <div class="contact-rule"></div>
    <div class="contact-bar"></div>

    <ul class="contacts">
      <li>
        <svg viewBox="0 0 24 24" aria-hidden="true"><path d="M6.6 10.8a15 15 0 0 0 6.6 6.6l2.2-2.2a1 1 0 0 1 1-.25 11.4 11.4 0 0 0 3.6.57 1 1 0 0 1 1 1V20a1 1 0 0 1-1 1A17 17 0 0 1 3 4a1 1 0 0 1 1-1h3.5a1 1 0 0 1 1 1c0 1.25.2 2.45.57 3.57a1 1 0 0 1-.25 1z"/></svg>
        <span>(+571) 555 010 2030</span>
      </li>
      <li>
        <svg viewBox="0 0 24 24" aria-hidden="true"><path d="M2 5h20v14H2zm2 2v.5l8 5 8-5V7zm0 2.8V17h16V9.8l-8 5z"/></svg>
        <span>info@ulmira-example.com</span>
      </li>
      <li>
        <svg viewBox="0 0 24 24" aria-hidden="true"><path d="M12 2a10 10 0 1 0 0 20 10 10 0 0 0 0-20zm0 2c.9 1.2 1.6 2.6 2 4h-4c.4-1.4 1.1-2.8 2-4zM4.3 14a8 8 0 0 1 0-4h3.4a16 16 0 0 0 0 4zm.9 2h3c.3 1.3.8 2.5 1.4 3.6A8 8 0 0 1 5.2 16zm3-8h-3a8 8 0 0 1 4.4-3.6C8.9 5.5 8.5 6.7 8.2 8zM12 20c-.9-1.2-1.6-2.6-2-4h4c-.4 1.4-1.1 2.8-2 4zm2.3-6H9.7a14 14 0 0 1 0-4h4.6a14 14 0 0 1 0 4zm.1 5.6c.6-1.1 1.1-2.3 1.4-3.6h3a8 8 0 0 1-4.4 3.6zm1.9-5.6a16 16 0 0 0 0-4h3.4a8 8 0 0 1 0 4z"/></svg>
        <span>www.ulmira-example.com</span>
      </li>
    </ul>

    <div class="bottom-band"></div>
  </section>

</main>
</body>
</html>
```